furniture and home contents restoration

I need to list the services that we perform in our studio.
we serve the general public as well as the insurance/ remediation industry

```html
<!DOCTYPE html>
<html lang="en">
<head>
<meta charset="utf-8">
<title>Paramount Restorers – Business Cards</title>
<link href="https://fonts.googleapis.com/css2?family=PT+Serif:wght@400;700&display=swap" rel="stylesheet">
<style>
  :root {
    --backdrop: #c8c3bc;
    --card: #1f303a;
    --ink: #f3f1ec;
    --shadow: rgba(0,0,0,0.28);
  }
  * { box-sizing: border-box; margin: 0; padding: 0; }
  html, body {
    width: 1200px; height: 930px; overflow: hidden;
    background: var(--backdrop);
    font-family: "PT Serif", Georgia, serif;
    color: var(--ink);
  }
  .canvas { position: relative; width: 1200px; height: 930px; }
  .card {
    position: absolute; left: 250px;
    width: 700px; height: 400px;
    background: var(--card);
    border-radius: 16px;
    box-shadow: 0 6px 14px var(--shadow);
  }
  .card--services { top: 48px; }
  .card--contact { top: 482px; }

  /* Services side */
  .services__title {
    position: absolute; top: 34px; left: 0; right: 0;
    text-align: center; font-weight: 700; font-size: 31px; letter-spacing: 1px;
  }
  .services__list {
    position: absolute; top: 100px; list-style: none;
    font-size: 12.5px; line-height: 19px; text-transform: uppercase; letter-spacing: 0.3px;
  }
  .services__list--left { left: 40px; }
  .services__list--right { left: 372px; }
  .services__list li::before { content: "•"; margin-right: 6px; }
  .services__footer {
    position: absolute; bottom: 34px; left: 0; right: 0;
    text-align: center; font-size: 16px; line-height: 22px; text-transform: uppercase;
  }

  /* Contact side */
  .brand {
    position: absolute; left: 40px; top: 128px; width: 320px;
    text-align: center; font-weight: 700; font-size: 42px; line-height: 46px; letter-spacing: 1px;
  }
  .divider {
    position: absolute; left: 382px; top: 64px;
    width: 2px; height: 230px; background: var(--ink);
  }
  .person {
    position: absolute; left: 410px; top: 64px; width: 270px;
  }
  .person__name { font-weight: 700; font-size: 24px; letter-spacing: 0.5px; margin-bottom: 10px; }
  .contact { list-style: none; font-size: 15px; line-height: 22px; }
  .contact li { display: flex; align-items: center; gap: 8px; }
  .contact svg { width: 12px; height: 12px; flex: none; }
  .tagline { margin-top: 16px; font-size: 15px; line-height: 19px; }
  .specialty {
    position: absolute; left: 0; right: 0; bottom: 40px;
    text-align: center; font-size: 21px; text-transform: uppercase; letter-spacing: 0.5px;
  }
</style>
</head>
<body>
<main class="canvas">

  <section class="card card--services">
    <h2 class="services__title">PARAMOUNT RESTORERS</h2>
    <ul class="services__list services__list--left">
      <li>Antique repair and restoration</li>
      <li>Art cleaning and remounting</li>
      <li>Art and mirror frame repair</li>
      <li>Chandelier cleaning and restoration</li>
      <li>Document restoration</li>
      <li>Glass, ceramic, and mirror repair</li>
      <li>Hardware repair and restoration</li>
      <li>Kitchen removal and reinstallation</li>
      <li>Lamp cleaning and restoration</li>
      <li>Lamp shade replacement</li>
    </ul>
    <ul class="services__list services__list--right">
      <li>Metal polishing and restoration</li>
      <li>Odor removal and ozone services</li>
      <li>Photo restoration</li>
      <li>Upholstery cleaning and deodorizing</li>
      <li>In-house upholstery and reupholstery</li>
      <li>Rug cleaning and restoration</li>
      <li>Musical instrument restoration</li>
      <li>Window treatment repair/ restoration</li>
      <li>Leather restoration and replacement</li>
      <li>Piano restoration and repair</li>
    </ul>
    <p class="services__footer">On-site inspections and desk review services<br>Assessment reports and estimates for repair and restoration</p>
  </section>

  <section class="card card--contact">
    <h1 class="brand">PARAMOUNT<br>RESTORERS</h1>
    <div class="divider"></div>
    <div class="person">
      <h2 class="person__name">DANIEL MORETTI</h2>
      <ul class="contact">
        <li><svg viewBox="0 0 12 12"><path d="M2 1l2 0 1 3-1.3 1a7 7 0 0 0 3.3 3.3L8 7l3 1 0 2c0 .6-.5 1-1 1A9 9 0 0 1 1 2c0-.5.4-1 1-1z" fill="#f3f1ec"/></svg>555 201 4400</li>
        <li><svg viewBox="0 0 12 12"><rect x="3" y="1" width="6" height="10" rx="1" fill="none" stroke="#f3f1ec" stroke-width="1.3"/></svg>555 318 7265</li>
        <li><svg viewBox="0 0 12 12"><rect x="3" y="1" width="6" height="3" fill="none" stroke="#f3f1ec"/><rect x="1" y="4" width="10" height="5" rx="1" fill="#f3f1ec"/><rect x="3" y="8" width="6" height="3" fill="none" stroke="#f3f1ec"/></svg>555 201 4460</li>
        <li><svg viewBox="0 0 12 12"><path d="M6 11S2 7 2 4.5a4 4 0 0 1 8 0C10 7 6 11 6 11z" fill="#f3f1ec"/><circle cx="6" cy="4.5" r="1.4" fill="#1f303a"/></svg>18 brookside ave. milford, ny 10599</li>
        <li><svg viewBox="0 0 12 12"><rect x="1" y="2.5" width="10" height="7" fill="none" stroke="#f3f1ec" stroke-width="1.2"/><path d="M1 2.5l5 4 5-4" fill="none" stroke="#f3f1ec" stroke-width="1.2"/></svg>paramountrest@mail.com</li>
      </ul>
      <p class="tagline">serving the general public and the<br>insurance industry for over 40 years</p>
    </div>
    <p class="specialty">Home contents restoration</p>
  </section>

</main>
</body>
</html>
```